Corporate Business Card

Very professional, Modern, Not to busy, include phone address email, website
(253) 617-4930, 18761 52nd Avenue S, Alder Falls, OR 98047, martin@plumlinegroup.com, varkoworks.com

Target Market(s)

Manufacturing

Industry/Entity Type

Aero, machining, manufacturing, Off road racing

Contact Information for Business Card

Phone, address email, website

```html
<!DOCTYPE html>
<html lang="en">
<head>
<meta charset="utf-8">
<title>Varko Works – Business Card</title>
<link href="https://fonts.googleapis.com/css2?family=Exo+2:wght@700&family=Roboto:wght@400&display=swap" rel="stylesheet">
<style>
  :root {
    --backdrop: #2a2a2a;
    --navy: #283868;
    --red: #bb2026;
    --silver: #a3a5a8;
    --white: #f4f4f4;
    --ink-dark: #1a1d26;
  }
  html, body {
    margin: 0;
    padding: 0;
    width: 1200px;
    height: 1138px;
    overflow: hidden;
    background: var(--backdrop);
  }
  .canvas {
    position: relative;
    width: 1200px;
    height: 1138px;
  }
  .card {
    position: absolute;
    width: 620px;
    height: 376px;
    border-radius: 16px;
    overflow: hidden;
    background: var(--navy);
  }
  .card-front { left: 274px; top: 186px; }
  .card-back  { left: 276px; top: 608px; }

  .front-name {
    position: absolute;
    left: 0; right: 0;
    top: 108px;
    text-align: center;
    font-family: "Exo 2", sans-serif;
    font-weight: 700;
    font-size: 66px;
    letter-spacing: 2px;
    color: var(--ink-dark);
    margin: 0;
  }
  .front-url {
    position: absolute;
    left: 0; right: 0;
    top: 322px;
    text-align: center;
    font-family: "Roboto", sans-serif;
    font-size: 17px;
    letter-spacing: 9px;
    color: var(--white);
    margin: 0;
  }
  .front-url .accent { color: var(--red); }

  .back-wave {
    position: absolute;
    inset: 0;
    width: 620px;
    height: 376px;
  }
  .back-name {
    position: absolute;
    left: 52px;
    top: 72px;
    font-family: "Exo 2", sans-serif;
    font-weight: 700;
    font-size: 40px;
    letter-spacing: 1px;
    color: var(--white);
    margin: 0;
  }
  .person {
    position: absolute;
    right: 28px;
    top: 196px;
    font-family: "Exo 2", sans-serif;
    font-weight: 700;
    font-size: 26px;
    letter-spacing: 0.5px;
    color: var(--white);
    margin: 0;
  }
  .contact {
    position: absolute;
    right: 28px;
    top: 248px;
    margin: 0;
    padding: 0;
    list-style: none;
    font-family: "Roboto", sans-serif;
    font-size: 16.5px;
    color: var(--white);
    text-align: right;
  }
  .contact li {
    display: flex;
    justify-content: flex-end;
    align-items: center;
    gap: 12px;
    height: 24px;
  }
  .contact .address { margin-top: 5px; }
  .contact svg { width: 16px; height: 16px; fill: var(--white); }
</style>
</head>
<body>
<main class="canvas">
  <section class="card card-front">
    <h1 class="front-name">VARKO WORKS</h1>
    <p class="front-url">www.varko<span class="accent">works</span>.com</p>
  </section>

  <section class="card card-back">
    <svg class="back-wave" viewBox="0 0 620 376" aria-hidden="true">
      <path fill="var(--silver)" d="M0,212 C150,262 280,222 400,132 C470,90 540,82 620,96 L620,376 L0,376 Z"/>
      <path fill="var(--navy)" d="M0,238 C150,288 280,248 400,158 C470,114 540,106 620,112 L620,376 L0,376 Z"/>
      <path fill="var(--red)" d="M0,252 C150,300 280,262 400,172 C470,128 540,118 620,124 L620,376 L0,376 Z"/>
    </svg>

    <h2 class="back-name">VARKO WORKS</h2>
    <p class="person">MARTIN HALE</p>
    <ul class="contact">
      <li>(253) 617-4930
        <svg viewBox="0 0 16 16"><path d="M2 6c0-2 2-3 6-3s6 1 6 3v1h-3V5.5H5V7H2zM4 8h8l2 5H2z"/></svg>
      </li>
      <li>www.varkoworks.com
        <svg viewBox="0 0 16 16"><path d="M1 3h14v10H1zM2.5 4.5v.3L8 9l5.5-4.2v-.3zM2.5 6.6v5h11v-5L8 10.8z"/></svg>
      </li>
      <li>martin@plumlinegroup.com
        <svg viewBox="0 0 16 16"><circle cx="8" cy="8" r="6.5" fill="none" stroke="#f4f4f4" stroke-width="1.3"/><path d="M1.5 8h13M8 1.5v13" stroke="#f4f4f4" stroke-width="1.1"/><ellipse cx="8" cy="8" rx="3" ry="6.5" fill="none" stroke="#f4f4f4" stroke-width="1.1"/></svg>
      </li>
      <li class="address">18761 52nd Avenue S, Alder Falls, OR 98047</li>
    </ul>
  </section>
</main>
</body>
</html>
```